Rosko Tamblin

I am a songwriter and would like to include a bio, pictures, discography, CD covers and access to some of my music

Target Market(s)

Music Lovers, songwriters publishers

Coding

Coded - Design and coding required

Number of Pages Required

5+ page

Requirements
Must have
• Pictures of my CD covers, pictures of me and either my Music or links to my music
Nice to have
Should not have
• cartoons

```html
<!DOCTYPE html>
<html lang="en">
<head>
<meta charset="utf-8">
<title>Rosko Tamblin — Songwriter</title>
<link href="https://fonts.googleapis.com/css2?family=Playfair+Display:wght@400;700;900&family=Open+Sans:ital,wght@0,400;0,600;0,700;1,400;1,600&display=swap" rel="stylesheet">
<style>
:root{
  --red:#c0141b;
  --red-dark:#8e0d12;
  --black:#000;
  --ink:#0a0a0a;
  --footer:#161616;
  --white:#fff;
  --grey:#cfcfcf;
  --muted:#9a9a9a;
  --serif:"Playfair Display", Georgia, serif;
  --sans:"Open Sans", Arial, sans-serif;
}
*{margin:0;padding:0;box-sizing:border-box}
html,body{width:1200px;height:4539px;overflow:hidden;background:var(--black);color:var(--white);font-family:var(--sans)}
.page{position:relative;width:1200px;height:4539px}
section,footer{position:absolute;left:0;width:1200px;overflow:hidden}
.abs{position:absolute}
.btn{position:absolute;display:flex;align-items:center;justify-content:center;gap:8px;background:var(--red);color:var(--white);border-radius:24px;font:700 15px var(--sans);text-transform:uppercase}
.btn svg{width:14px;height:14px}
.section-title{position:absolute;left:0;width:1200px;text-align:center;font:900 38px var(--serif);text-transform:uppercase;letter-spacing:.5px}
.title-rule{position:absolute;left:570px;width:60px;height:3px;background:var(--red)}
.title-rule.light{background:var(--white)}
.ph{position:absolute}

/* hero */
.hero{top:0;height:600px}
.hero-photo{inset:0;background:linear-gradient(100deg,#1a1410 0%,#4a3828 35%,#7a5c3e 55%,#3a4a5e 72%,#1c2330 100%)}
.hero-shade{position:absolute;inset:0;background:linear-gradient(90deg,rgba(0,0,0,.55),rgba(0,0,0,.1) 60%,rgba(0,0,0,.3))}
.brand{position:absolute;left:111px;top:96px;font:400 27px var(--serif);color:var(--red);letter-spacing:.5px;text-transform:uppercase}
.brand-dot{position:absolute;left:221px;top:28px;width:26px;height:26px;border-radius:50%;background:var(--red)}
.social{position:absolute;width:38px;height:38px;border-radius:50%;background:var(--white);top:36px}
.nav{position:absolute;top:107px;display:flex;font:600 14px var(--sans)}
.nav a{position:absolute;white-space:nowrap;color:var(--white);text-decoration:none}
.hero h1{position:absolute;left:111px;top:258px;font:900 44px/1.1 var(--serif);text-transform:uppercase}
.dots{position:absolute;display:flex;gap:8px;align-items:center}
.dots i{display:block;width:10px;height:10px;border-radius:50%;background:var(--white)}
.dots i.on{width:14px;height:14px}
.dots.red i.on{background:var(--red)}

/* about */
.about{top:600px;height:580px;background:var(--black)}
.about-divider{left:580px;top:80px;width:2px;height:410px;background:#8a8a8a}
.about h2{position:absolute;left:625px;top:98px;font:900 38px/1.18 var(--serif);text-transform:uppercase}
.about p{position:absolute;left:625px;top:198px;width:457px;font:400 14px/28px var(--sans);text-align:justify;color:var(--grey)}

/* cd covers */
.covers{top:1180px;height:835px;background:radial-gradient(ellipse at 50% 0%,#3a2a30 0%,#1c1418 40%,#0a0808 80%)}
.cover{position:absolute;width:311px}
.cover-art{position:absolute;left:0;top:0;width:311px}
.cover-label{position:absolute;left:0;width:311px;height:32px;background:var(--red-dark);display:flex;align-items:center;justify-content:center;font:700 16px var(--sans);text-transform:uppercase}
.feature{position:absolute;background:var(--red-dark);text-align:center}
.feature h3{font:700 19px var(--sans);text-transform:uppercase;margin-top:100px}
.feature p{font:400 13px/26px var(--sans);margin:10px auto 0;width:270px}

/* testimonials */
.testimonials{top:2015px;height:665px;background:var(--black)}
.eyebrow{position:absolute;left:0;width:1200px;text-align:center;color:var(--red);font:400 15px var(--sans);letter-spacing:.5px}
.quote{position:absolute;left:83px;top:265px;width:550px;font:italic 600 14px/28px var(--sans);text-align:justify;color:var(--grey)}
.reviewer{position:absolute;left:83px;top:474px;font:700 14px var(--sans);display:flex;gap:14px;align-items:center}
.stars{color:var(--red);letter-spacing:2px;font-size:16px}

/* gallery */
.gallery{top:2680px;height:840px;background:radial-gradient(ellipse at 50% 10%,#3a2c34 0%,#1a1216 45%,#080606 85%)}

/* discography */
.discography{top:3520px;height:645px;background:var(--black)}
.album{position:absolute;width:240px;text-align:center}
.disc{position:relative;margin:0 auto;width:176px;height:176px;border-radius:50%;border:2px solid #bdbdbd;padding:6px}
.disc .art{width:100%;height:100%;border-radius:50%}
.disc .play{position:absolute;left:70px;top:70px;width:36px;height:36px;border-radius:50%;background:var(--white)}
.album .year{margin-top:20px;font:400 16px var(--sans)}
.album h4{margin-top:6px;font:700 17px var(--sans);text-transform:uppercase;color:var(--white)}
.album p{margin-top:4px;font:400 13px var(--sans);color:var(--grey)}
.tools{display:flex;gap:12px;justify-content:center;margin-top:16px}
.tool{width:30px;height:30px;border-radius:50%;border:1.5px solid #bdbdbd;display:flex;align-items:center;justify-content:center}
.tool i{display:block;width:12px;height:12px;border-radius:50%;background:var(--white)}
.tool svg{width:14px;height:14px}

/* footer */
.site-footer{top:4165px;height:374px;background:var(--footer)}
.footer-brand{position:absolute;left:111px;top:160px;font:400 27px var(--serif);color:var(--red);text-transform:uppercase}
.footer-about{position:absolute;left:111px;top:204px;width:330px;font:400 12px/19px var(--sans);color:var(--grey)}
.col{position:absolute;top:71px}
.col h5{font:700 15px var(--sans)}
.col .rule{width:40px;height:2px;background:var(--red);margin:8px 0 14px}
.col li{list-style:none;font:400 12px/30px var(--sans);color:var(--grey)}
.col p{font:400 12px/19px var(--sans);color:var(--grey);width:190px}
.col b{display:block;font:700 12px/19px var(--sans);color:var(--white)}
.footer-rule{position:absolute;left:111px;top:305px;width:982px;height:1px;background:#555}
.copyright{position:absolute;left:0;top:340px;width:1200px;text-align:center;font:400 12px var(--sans);color:var(--grey)}
</style>
</head>
<body>
<div class="page">

<svg width="0" height="0" style="position:absolute">
  <defs>
    <symbol id="note" viewBox="0 0 16 16"><path d="M6 2 L15 0 V11.5 A2.5 2 0 1 1 13 9.6 V3.4 L8 4.5 V13.5 A2.5 2 0 1 1 6 11.6 Z" fill="#fff"/></symbol>
  </defs>
</svg>

<!-- HERO -->
<section class="hero">
  <div class="ph hero-photo" role="img" aria-label="Songwriter writing on sheet music with a pencil while holding an electric guitar"></div>
  <div class="hero-shade"></div>
  <span class="brand-dot"></span>
  <div class="brand">Rosko Tamblin</div>
  <span class="social" style="left:654px"></span>
  <span class="social" style="left:703px"></span>
  <span class="social" style="left:751px"></span>
  <span class="social" style="left:800px"></span>
  <div class="btn" style="left:858px;top:30px;width:229px;height:48px"><svg><use href="#note"/></svg>Download Songs</div>
  <nav class="nav">
    <a style="left:465px">About Rosko Tamblin</a>
    <a style="left:668px">Gallery</a>
    <a style="left:765px">Discography</a>
    <a style="left:901px">Cd Covers</a>
    <a style="left:1017px">My Music</a>
  </nav>
  <div class="abs" style="left:990px;top:100px;width:1px;height:30px;background:#fff"></div>
  <h1>Discover the Magic<br>of Music</h1>
  <div class="btn" style="left:111px;top:376px;width:191px;height:46px"><svg><use href="#note"/></svg>Get Started</div>
  <div class="dots" style="left:558px;top:553px"><i></i><i></i><i class="on"></i><i></i><i></i></div>
</section>

<!-- ABOUT -->
<section class="about">
  <svg class="abs" style="left:90px;top:115px" width="430" height="345" viewBox="0 0 430 345">
    <defs><radialGradient id="fire" cx="50%" cy="55%" r="60%"><stop offset="0" stop-color="#f0a030"/><stop offset=".6" stop-color="#a8301a"/><stop offset="1" stop-color="#1a0806"/></radialGradient></defs>
    <ellipse cx="213" cy="175" rx="207" ry="167" fill="url(#fire)"/>
    <path d="M40 250 C-10 130 120 10 300 30" fill="none" stroke="#111" stroke-width="9"/>
  </svg>
  <div class="abs" style="left:90px;top:115px;width:430px;height:345px" role="img" aria-label="Portrait of Rosko Tamblin standing in front of a glowing fire crater"></div>
  <div class="abs about-divider"></div>
  <h2>About<br>Rosko Tamblin</h2>
  <p>Rosko Tamblin was born and raised in Houston, Texas. He began playing music at the age of eight when his sister returned home from summer camp and asked her parents to buy her a baritone ukulele. She taught her younger brother some chords on the ukulele and he was hooked. The following spring, they went to one of the border towns in Mexico and bought a Mexican guitar for $12. They restrung it with nylon strings</p>
  <div class="btn" style="left:625px;top:418px;width:183px;height:47px"><svg><use href="#note"/></svg>Learn More</div>
</section>

<!-- CD COVERS -->
<section class="covers" role="region" aria-label="CD covers">
  <div class="ph" style="inset:0;background:linear-gradient(180deg,rgba(0,0,0,0) 60%,rgba(0,0,0,.6))" role="img" aria-label="Concert crowd under stage lights"></div>
  <div class="section-title" style="top:76px">CD Covers</div>
  <div class="title-rule" style="top:136px"></div>

  <div class="cover" style="left:111px;top:174px">
    <div class="ph cover-art" style="height:246px;background:linear-gradient(135deg,#25c07a,#d8e040 40%,#e04a7a 75%,#3050d0)" role="img" aria-label="The Tamblins album cover, musician with a mandolin on a colourful background"></div>
  </div>
  <div class="feature" style="left:111px;top:420px;width:311px;height:240px">
    <svg class="abs" style="left:126px;top:28px" width="60" height="52" viewBox="0 0 60 52"><circle cx="26" cy="28" r="21" fill="none" stroke="#fff" stroke-width="2"/><circle cx="26" cy="28" r="11" fill="none" stroke="#fff" stroke-width="2"/><circle cx="26" cy="28" r="3" fill="#fff"/><path d="M44 4 L58 2 V16 M44 4 V18" fill="none" stroke="#fff" stroke-width="2"/></svg>
    <h3>The Tamblins</h3>
    <p>Lorem ipsum dolor sit amet, tetur adipiscing elit, sed do eiusmod temp cididunt ut labore et dolore magna aliqua.</p>
  </div>

  <div class="cover" style="left:446px;top:174px">
    <div class="ph cover-art" style="height:198px;background:linear-gradient(160deg,#e8a020,#c83818 45%,#2a1a14)" role="img" aria-label="Rex Walden album cover with flames and a coffee cup"></div>
    <div class="cover-label" style="top:198px">Rex Walden</div>
  </div>
  <div class="cover" style="left:780px;top:174px">
    <div class="ph cover-art" style="height:198px;background:linear-gradient(160deg,#3a3a3a,#9a9a9a 50%,#1a1a1a)" role="img" aria-label="Harbor Lane album cover, black and white guitarist with pine trees"></div>
    <div class="cover-label" style="top:198px">Harbor Lane</div>
  </div>
  <div class="cover" style="left:446px;top:430px">
    <div class="ph cover-art" style="height:198px;background:linear-gradient(160deg,#5a6a80,#a04030 55%,#1a1414)" role="img" aria-label="Quiet Hours Road album cover, silhouette under a stormy sky"></div>
    <div class="cover-label" style="top:198px">Quiet Hours Road</div>
  </div>
  <div class="cover" style="left:780px;top:430px">
    <div class="ph cover-art" style="height:198px;background:linear-gradient(170deg,#6a8aa0,#3a5a6a 50%,#1a2a30)" role="img" aria-label="Northbound Tide Song album cover, waves crashing on rocks"></div>
    <div class="cover-label" style="top:198px">Northbound Tide Song</div>
  </div>

  <div class="btn" style="left:476px;top:698px;width:248px;height:47px"><svg><use href="#note"/></svg>View More Cover Art</div>
</section>

<!-- TESTIMONIALS -->
<section class="testimonials">
  <div class="eyebrow" style="top:84px">TESTIMONIALS</div>
  <div class="section-title" style="top:118px">From the Community</div>
  <div class="title-rule" style="top:182px"></div>
  <svg class="abs" style="left:83px;top:222px" width="28" height="22" viewBox="0 0 28 22"><path d="M12 0 C4 2 0 8 0 14 A6 6 0 1 0 6 8 C7 5 9 3 12 2Z M28 0 C20 2 16 8 16 14 A6 6 0 1 0 22 8 C23 5 25 3 28 2Z" fill="#c0141b"/></svg>
  <p class="quote">Yet another great song from Rosko! An unlimited catalog of excellent work. Pleasure every time Yet another great experience! 5 stars, as always. Always a great day for me when I have one of Rosko's songs on my calendar. Thoroughly enjoy each one every time! Yet another great project from Rosko! I'm amazed at the breadth of his catalog. Always enjoyable working on his music! Rosko is quickly becoming one of my favorite clients (can I say that?) Smooth process every time, friendly exchanges, and great music to work on.</p>
  <svg class="abs" style="left:506px;top:450px" width="28" height="22" viewBox="0 0 28 22"><path d="M16 22 C24 20 28 14 28 8 A6 6 0 1 0 22 14 C21 17 19 19 16 20Z M0 22 C8 20 12 14 12 8 A6 6 0 1 0 6 14 C5 17 3 19 0 20Z" fill="#c0141b"/></svg>
  <div class="reviewer">Mara Quillen Keyboards <span class="stars">★★★★★</span></div>
  <div class="abs" style="left:666px;top:228px;width:2px;height:308px;background:#8a8a8a"></div>
  <div class="ph" style="left:705px;top:255px;width:420px;height:340px;border-radius:50%;background:radial-gradient(ellipse,#d8d8d8,#6a6a6a 55%,#1a1a1a)" role="img" aria-label="Black and white illustration of a guitarist in a hat"></div>
  <div class="dots red" style="left:558px;top:573px"><i></i><i></i><i class="on"></i><i></i><i></i></div>
</section>

<!-- GALLERY -->
<section class="gallery">
  <div class="section-title" style="top:74px">Our Gallery</div>
  <div class="title-rule light" style="top:134px"></div>
  <div class="ph" style="left:111px;top:175px;width:229px;height:228px;background:linear-gradient(135deg,#3a5a78,#c08a50)" role="img" aria-label="Acoustic guitar resting on a notebook"></div>
  <div class="ph" style="left:359px;top:175px;width:231px;height:228px;background:linear-gradient(135deg,#5a4a3e,#2a2420)" role="img" aria-label="Instruments and keyboard laid out on a wooden floor"></div>
  <div class="ph" style="left:608px;top:175px;width:230px;height:228px;background:linear-gradient(135deg,#d8d0c4,#3a3a3a)" role="img" aria-label="Guitarist writing lyrics on paper"></div>
  <div class="ph" style="left:856px;top:175px;width:231px;height:228px;background:linear-gradient(135deg,#7a5638,#3a2a1e)" role="img" aria-label="Headphones, coffee cup and CD on a wooden desk"></div>
  <div class="ph" style="left:111px;top:420px;width:229px;height:228px;background:linear-gradient(135deg,#e8e4dc,#a08a6a)" role="img" aria-label="Hand writing songs beside a straw hat"></div>
  <div class="ph" style="left:359px;top:420px;width:231px;height:228px;background:linear-gradient(135deg,#1a1a1a,#8a8a8a)" role="img" aria-label="Hands playing a piano keyboard"></div>
  <div class="ph" style="left:608px;top:420px;width:230px;height:228px;background:linear-gradient(135deg,#c8a060,#e8e8e8)" role="img" aria-label="Hand writing music next to a guitar"></div>
  <div class="ph" style="left:856px;top:420px;width:231px;height:228px;background:linear-gradient(135deg,#c05a2a,#e0a060)" role="img" aria-label="Person playing an acoustic guitar"></div>
  <div class="btn" style="left:478px;top:705px;width:244px;height:47px"><svg><use href="#note"/></svg>View More &nbsp;Pictures</div>
</section>

<!-- DISCOGRAPHY -->
<section class="discography">
  <div class="section-title" style="top:72px">Discography</div>
  <div class="title-rule" style="top:133px"></div>

  <div class="album" style="left:96px;top:162px">
    <div class="disc"><div class="art" style="background:radial-gradient(circle,#e04a7a,#3a3a9a 70%)" role="img" aria-label="Album art, musician on a colourful background"></div><span class="play"></span><svg class="abs" style="left:82px;top:79px" width="16" height="18"><path d="M0 0 L16 9 L0 18Z" fill="#000"/></svg></div>
    <div class="year">2015</div><h4>Lorem Ipsum</h4><p>Lorem ipsum dolor sit amet,</p>
    <div class="tools"><span class="tool"><i></i></span><span class="tool"><svg viewBox="0 0 14 14"><path d="M4 2 L12 7 L4 12Z" fill="none" stroke="#fff" stroke-width="1.4"/></svg></span><span class="tool"><svg viewBox="0 0 14 14"><path d="M7 1 V9 M3.5 5.5 L7 9 L10.5 5.5 M2 12.5 H12" fill="none" stroke="#fff" stroke-width="1.4"/></svg></span></div>
  </div>
  <div class="album" style="left:352px;top:162px">
    <div class="disc"><div class="art" style="background:radial-gradient(circle,#7a8aa0,#2a2a3a 70%)" role="img" aria-label="Album art, silhouette under a stormy sky"></div><span class="play"></span><svg class="abs" style="left:82px;top:79px" width="16" height="18"><path d="M0 0 L16 9 L0 18Z" fill="#000"/></svg></div>
    <div class="year">2015</div><h4>Lorem Ipsum</h4><p>Lorem ipsum dolor sit amet,</p>
    <div class="tools"><span class="tool"><i></i></span><span class="tool"><svg viewBox="0 0 14 14"><path d="M4 2 L12 7 L4 12Z" fill="none" stroke="#fff" stroke-width="1.4"/></svg></span><span class="tool"><svg viewBox="0 0 14 14"><path d="M7 1 V9 M3.5 5.5 L7 9 L10.5 5.5 M2 12.5 H12" fill="none" stroke="#fff" stroke-width="1.4"/></svg></span></div>
  </div>
  <div class="album" style="left:608px;top:162px">
    <div class="disc"><div class="art" style="background:radial-gradient(circle,#c08040,#3a4a6a 70%)" role="img" aria-label="Album art with a painted landscape"></div><span class="play"></span><svg class="abs" style="left:82px;top:79px" width="16" height="18"><path d="M0 0 L16 9 L0 18Z" fill="#000"/></svg></div>
    <div class="year">2015</div><h4>Lorem Ipsum</h4><p>Lorem ipsum dolor sit amet,</p>
    <div class="tools"><span class="tool"><i></i></span><span class="tool"><svg viewBox="0 0 14 14"><path d="M4 2 L12 7 L4 12Z" fill="none" stroke="#fff" stroke-width="1.4"/></svg></span><span class="tool"><svg viewBox="0 0 14 14"><path d="M7 1 V9 M3.5 5.5 L7 9 L10.5 5.5 M2 12.5 H12" fill="none" stroke="#fff" stroke-width="1.4"/></svg></span></div>
  </div>
  <div class="album" style="left:864px;top:162px">
    <div class="disc"><div class="art" style="background:radial-gradient(circle,#a8a0b8,#5a5070 70%)" role="img" aria-label="Album art with soft purple tones"></div><span class="play"></span><svg class="abs" style="left:82px;top:79px" width="16" height="18"><path d="M0 0 L16 9 L0 18Z" fill="#000"/></svg></div>
    <div class="year">2015</div><h4>Lorem Ipsum</h4><p>Lorem ipsum dolor sit amet,</p>
    <div class="tools"><span class="tool"><i></i></span><span class="tool"><svg viewBox="0 0 14 14"><path d="M4 2 L12 7 L4 12Z" fill="none" stroke="#fff" stroke-width="1.4"/></svg></span><span class="tool"><svg viewBox="0 0 14 14"><path d="M7 1 V9 M3.5 5.5 L7 9 L10.5 5.5 M2 12.5 H12" fill="none" stroke="#fff" stroke-width="1.4"/></svg></span></div>
  </div>

  <div class="btn" style="left:505px;top:515px;width:190px;height:47px"><svg><use href="#note"/></svg>Play More</div>
</section>

<!-- FOOTER -->
<footer class="site-footer">
  <span class="abs" style="left:221px;top:90px;width:26px;height:26px;border-radius:50%;background:var(--red)"></span>
  <div class="footer-brand">Rosko Tamblin</div>
  <p class="footer-about">Lorem ipsum dolor sit amet, consectetur adipiscing elit, sed do eiusmod tempor incididunt</p>
  <div class="btn" style="left:111px;top:254px;width:124px;height:40px;font-size:13px;text-transform:none">Ask Question</div>

  <div class="col" style="left:513px">
    <h5>Quick Links</h5><div class="rule"></div>
    <ul><li>About Rosko Tamblin</li><li>Gallery</li><li>Discography</li><li>Cd Covers</li><li>My Music</li></ul>
  </div>
  <div class="col" style="left:707px">
    <h5>Connect With US</h5><div class="rule"></div>
    <ul><li>Newsletter</li><li>Video Channel</li><li>Photo Feed</li><li>Pin Board</li></ul>
  </div>
  <div class="col" style="left:917px">
    <h5>Contact Us</h5><div class="rule"></div>
    <p>Feel free get in touch with us via phone or send us a message</p>
    <b style="margin-top:12px">555-010-2040</b>
    <b>info@roskotamblin.com</b>
  </div>
  <div class="footer-rule"></div>
  <div class="copyright">Rosko Tamblin Copyright © All right reserved</div>
</footer>

</div>
</body>
</html>
```